Tollin Waste Website Design

Our new start-up needs a website design. We plan to help businesses find more sustainable ways to manage their waste. Our initial website aims to gather contact data from potential business customers and comprehensive information from waste facilities and waste transporters. We have a logo design (attached) which we would like included in the website design. I have also attached a number of pages that describe what information should appear on each page as well as a web design brief file that describes the look we are after.

```html
<!DOCTYPE html>
<html lang="en">
<head>
<meta charset="utf-8">
<title>Tollin Waste Website Design</title>
<link href="https://fonts.googleapis.com/css2?family=Raleway:wght@400;500;600;700&display=swap" rel="stylesheet">
<style>
:root{
  --stage:#7ba52e;
  --leaf:#5b9328;
  --lime:#a4d23c;
  --ink:#1c1f1a;
  --white:#ffffff;
  --modal:#e3e3e1;
  --text-dark:#2b2b2b;
}
*{box-sizing:border-box;margin:0;padding:0}
html,body{width:1200px;height:2161px;overflow:hidden}
body{background:var(--stage);font-family:'Raleway',sans-serif;position:relative}
.screen{position:absolute;left:143px;width:919px;height:509px;overflow:hidden;box-shadow:0 6px 18px rgba(0,0,0,.25)}
.screen--desk{top:190px}
.screen--home{top:958px}
.screen--popup{top:1523px}
.backdrop{position:absolute;inset:0}
.backdrop--litter{background:
  radial-gradient(ellipse 55% 60% at 50% 45%,#3d6a22 0%,#2a4a1a 45%,transparent 75%),
  radial-gradient(circle at 10% 80%,#4d4f52 0%,transparent 30%),
  radial-gradient(circle at 90% 60%,#55585a 0%,transparent 30%),
  linear-gradient(#1d2419,#171b16)}
.backdrop--street{background:linear-gradient(160deg,#3a4852,#1f2a30 55%,#2f3d44)}
.header{position:absolute;left:0;right:0;top:0;height:120px}
.brand{position:absolute;left:100px;top:44px;display:flex;align-items:center;gap:10px;color:var(--white);font-weight:600;font-size:30px}
.brand-dot{width:34px;height:34px;border-radius:50%;background:var(--lime)}
.nav{position:absolute;right:100px;top:53px;display:flex;gap:18px;list-style:none}
.nav li{color:var(--white);font-weight:600;font-size:13.5px;text-transform:uppercase}
.welcome{position:absolute;left:0;right:0;top:138px;text-align:center;color:var(--white)}
.welcome h1{font-weight:600;font-size:35px}
.welcome p{font-size:20px;margin-top:10px}
.audiences{position:absolute;left:0;right:0;top:240px;display:flex;justify-content:center;gap:22px}
.audience{width:144px;height:144px;border-radius:50%;border:4px solid var(--lime);padding:4px}
.audience-inner{width:100%;height:100%;border-radius:50%;background:var(--leaf);color:var(--white);text-align:center;padding-top:22px;font-weight:600;font-size:17px;line-height:1.05}
.audience-inner svg{display:block;margin:6px auto 0}
.footer{position:absolute;left:0;right:0;top:448px;text-align:center;color:var(--white);font-size:13px}
.version{position:absolute;right:18px;bottom:30px;color:#cfd3cc;font-size:7px}
.dim{position:absolute;inset:0;background:rgba(0,0,0,.72)}
.screen--popup .header,.screen--popup .footer{opacity:.25}
.modal{position:absolute;left:219px;top:111px;width:481px;height:290px;background:var(--modal);border:3px solid var(--lime);text-align:center}
.modal-close{position:absolute;right:38px;top:14px;width:15px;height:15px;border:1px solid #555;border-radius:50%;font-size:9px;line-height:13px;color:#444}
.modal-brand{display:flex;justify-content:center;align-items:center;gap:8px;margin-top:36px;font-weight:600;font-size:26px;color:var(--text-dark)}
.modal-brand .brand-dot{width:28px;height:28px}
.modal p{width:350px;margin:22px auto 0;font-size:13px;line-height:22px;color:var(--text-dark)}
.email{display:block;width:303px;height:30px;margin:16px auto 0;border-radius:15px;border:1px solid #bbb;background:var(--white);font-family:inherit;font-size:9px;text-align:center;color:#555}
.subscribe{display:block;width:98px;height:26px;margin:15px auto 0;border:0;border-radius:13px;background:var(--leaf);color:var(--white);font-family:inherit;font-weight:700;font-size:10px;text-transform:uppercase}
</style>
</head>
<body>
<svg width="0" height="0" style="position:absolute">
  <defs>
    <g id="icon-recycle" fill="none" stroke="#fff" stroke-width="2" stroke-linejoin="round">
      <path d="M20 6 L28 19 L23 19"/><path d="M17 10 L12 18"/><path d="M10 24 L4 34 L18 34"/><path d="M22 34 L36 34 L30 24"/><path d="M14 6 L20 6 L17 11"/>
    </g>
    <g id="icon-bins" fill="none" stroke="#fff" stroke-width="2">
      <rect x="3" y="12" width="11" height="22"/><rect x="15" y="12" width="11" height="22"/><rect x="27" y="12" width="11" height="22"/>
      <path d="M3 12 Q8.5 4 14 12 M15 12 Q20.5 4 26 12 M27 12 Q32.5 4 38 12"/><path d="M18 28 L20.5 22 L23 28 Z"/>
    </g>
    <g id="icon-truck" fill="none" stroke="#fff" stroke-width="2" stroke-linejoin="round">
      <path d="M4 16 L24 8 L36 14 L36 26 L16 34 L4 28 Z"/><path d="M4 16 L16 22 L36 14 M16 22 L16 34"/><circle cx="10" cy="31" r="3"/><circle cx="30" cy="30" r="3"/>
    </g>
  </defs>
</svg>

<section class="screen screen--desk">
  <div class="backdrop backdrop--litter" role="img" aria-label="Photo of green ivy surrounded by discarded cans, bottles and plastic waste"></div>
  <header class="header">
    <div class="brand"><span class="brand-dot"></span>Tollin Waste</div>
    <ul class="nav"><li>About us</li><li>What we do</li><li>Resources</li><li>Contact us</li></ul>
  </header>
  <div class="welcome"><h1>Welcome to Tollin Waste</h1><p>Take control of your waste here:</p></div>
  <div class="audiences">
    <div class="audience"><div class="audience-inner">Waste<br>Producers<svg width="40" height="40" viewBox="0 0 40 40"><use href="#icon-recycle"/></svg></div></div>
    <div class="audience"><div class="audience-inner">Waste<br>Facilities<svg width="40" height="40" viewBox="0 0 40 40"><use href="#icon-bins"/></svg></div></div>
    <div class="audience"><div class="audience-inner">Waste<br>Transporters<svg width="40" height="40" viewBox="0 0 40 40"><use href="#icon-truck"/></svg></div></div>
  </div>
  <p class="footer">© 2018 Tollin Waste. All rights reserved. Terms &amp; Conditions</p>
  <span class="version">v1</span>
</section>

<section class="screen screen--home">
  <div class="backdrop backdrop--litter" role="img" aria-label="Photo of green ivy surrounded by discarded cans, bottles and plastic waste"></div>
  <header class="header">
    <div class="brand"><span class="brand-dot"></span>Tollin Waste</div>
    <ul class="nav"><li>About us</li><li>What we do</li><li>Resources</li><li>Contact us</li></ul>
  </header>
  <div class="welcome"><h1>Welcome to Tollin Waste</h1><p>Take control of your waste here:</p></div>
  <div class="audiences">
    <div class="audience"><div class="audience-inner">Waste<br>Producers<svg width="40" height="40" viewBox="0 0 40 40"><use href="#icon-recycle"/></svg></div></div>
    <div class="audience"><div class="audience-inner">Waste<br>Facilities<svg width="40" height="40" viewBox="0 0 40 40"><use href="#icon-bins"/></svg></div></div>
    <div class="audience"><div class="audience-inner">Waste<br>Transporters<svg width="40" height="40" viewBox="0 0 40 40"><use href="#icon-truck"/></svg></div></div>
  </div>
  <p class="footer">© 2018 Tollin Waste. All rights reserved. Terms &amp; Conditions</p>
  <span class="version">v1</span>
</section>

<section class="screen screen--popup">
  <div class="backdrop backdrop--street" role="img" aria-label="Photo of a waste worker in a street lined with wheelie bins"></div>
  <header class="header">
    <div class="brand"><span class="brand-dot"></span>Tollin Waste</div>
    <ul class="nav"><li>About us</li><li>What we do</li><li>Resources</li><li>Contact us</li></ul>
  </header>
  <p class="footer">© 2018 Tollin Waste. All rights reserved. Terms &amp; Conditions</p>
  <div class="dim"></div>
  <div class="modal">
    <span class="modal-close">x</span>
    <div class="modal-brand"><span class="brand-dot"></span>Tollin Waste</div>
    <p>Welcome to Tollin Waste. We are just getting started. Please register your email address to receive updates from us.</p>
    <input class="email" type="email" placeholder="Enter Email">
    <button class="subscribe" type="button">Subscribe</button>
  </div>
</section>
</body>
</html>
```